Business Card Design for Online Gift Business

Business card design for a new online Canadian company called "Harlow & Brine Gift Boxes" selling modern and luxurious gift boxes for every occasion. Items are sourced locally from talented socially-responsible Canadian artisans. Each gift is elegantly presented in a keepsake wood box to ensure a lasting impression.

Industry/Entity Type

E-Commerce

Contact Information for Business Card

Marla Whitcombe, Proprietor
Brookhaven, NB
403-555-2741
www.harlowandbrine.ca
hello@harlowandbrine.ca

Requirements
Must have
• Gifts from our hands, to your home
• Please also include the symbols for Facebook and Instagram
Nice to have
• **I have attached a few samples of background colors and font colors that I like. I hope this helps in a few directions to try.

```html
<!DOCTYPE html>
<html lang="en">
<head>
<meta charset="utf-8">
<title>Harlow &amp; Brine Gift Boxes – Business Card</title>
<link rel="stylesheet" href="https://fonts.googleapis.com/css2?family=Yellowtail&family=Dosis:wght@400;500&display=swap">
<style>
  :root {
    --backdrop: #a8b1b3;
    --card: #e0bea2;
    --ink: #5a2f16;
    --ink-soft: rgba(90, 47, 22, 0.08);
    --script: "Yellowtail", cursive;
    --sans: "Dosis", sans-serif;
  }
  * { box-sizing: border-box; margin: 0; padding: 0; }
  html, body { width: 1200px; height: 824px; overflow: hidden; }
  body {
    background: var(--backdrop);
    position: relative;
    color: var(--ink);
  }
  .card {
    position: absolute;
    top: 258px;
    width: 540px;
    height: 308px;
    background: var(--card);
    box-shadow: 0 10px 24px rgba(0, 0, 0, 0.18);
    overflow: hidden;
  }
  .card--back { left: 30px; }
  .card--front { left: 630px; }

  /* contact side */
  .back-mark {
    position: absolute;
    left: 160px;
    top: 60px;
    width: 200px;
    height: 200px;
    border-radius: 50%;
    background: var(--ink-soft);
  }
  .contact {
    position: absolute;
    left: 0;
    right: 0;
    top: 66px;
    text-align: center;
  }
  .contact__name {
    font-family: var(--script);
    font-size: 40px;
    line-height: 1.1;
    letter-spacing: 0.5px;
  }
  .contact__role {
    font-family: var(--script);
    font-size: 20px;
    line-height: 1.2;
    margin: 0 0 10px 170px;
  }
  .contact__line {
    font-family: var(--sans);
    font-size: 17px;
    line-height: 1.35;
    letter-spacing: 0.5px;
    text-transform: uppercase;
  }
  .social {
    display: flex;
    justify-content: center;
    gap: 6px;
    margin-top: 8px;
  }
  .social__dot {
    width: 17px;
    height: 17px;
    border: 1.5px solid var(--ink);
    border-radius: 50%;
  }

  /* brand side */
  .brand {
    position: absolute;
    left: 0;
    right: 0;
    top: 96px;
    display: flex;
    justify-content: center;
    align-items: center;
    gap: 14px;
  }
  .brand__dot {
    width: 14px;
    height: 14px;
    border-radius: 50%;
    background: var(--ink);
  }
  .brand__name {
    font-family: var(--sans);
    font-weight: 400;
    font-size: 40px;
    letter-spacing: 6px;
    text-transform: uppercase;
    color: var(--ink);
  }
  .tagline {
    position: absolute;
    left: 0;
    right: 0;
    top: 186px;
    text-align: center;
    font-family: var(--script);
    font-size: 26px;
    letter-spacing: 0.5px;
  }
</style>
</head>
<body>
  <section class="card card--back" aria-label="Business card, contact side">
    <div class="back-mark" aria-hidden="true"></div>
    <div class="contact">
      <p class="contact__name">Marla Whitcombe</p>
      <p class="contact__role">Proprietor</p>
      <p class="contact__line">403-555-2741</p>
      <p class="contact__line">www.harlowandbrine.ca</p>
      <p class="contact__line">Brookhaven, NB</p>
      <div class="social" aria-label="Social media">
        <span class="social__dot"></span>
        <span class="social__dot"></span>
      </div>
    </div>
  </section>

  <section class="card card--front" aria-label="Business card, brand side">
    <div class="brand">
      <span class="brand__dot" aria-hidden="true"></span>
      <span class="brand__name">Harlow &amp; Brine</span>
    </div>
    <p class="tagline">Gifts from our hands, to your home</p>
  </section>
</body>
</html>
```